Local Flower Farm Needs Business Card Design

I need business cards designed for a flower farm based in Eudora, Kansas.
Business Info:
We are a local cut flower farm located in Eudora, Kansas, founded by Corinne Haldwick. What started as a passion for agriculture and search for more joy in daily life has blossomed into a small business dedicated to providing the community with beautiful, fresh, and sustainable flowers. We specialize in local, seasonal blooms, ensuring that every petal reflects the care and dedication we pour into our craft. Our mission is to deliver the highest quality flowers directly to our customers through local farmers markets and to florists who share our commitment to sustainability. Join us in celebrating the beauty of nature, one bloom at a time!
Contact Details:
Corinne Haldwick
Owner
Phone 913-555-0147
Facebook: Rosalind Thorpe Gardens
Instagram: @RosalindThorpeGardens
Website: RosalindThorpeGardens.example
Target Market(s)
Wholesale to Florists and Direct to Consumer via Farmers Market
Industry/Entity Type
Florist, Farm
Contact Information for Business Card
Name, Contact Info, Logo
Look and feel
Each slider illustrates characteristics of the customer's brand and the style your logo design should communicate.

```html
<!DOCTYPE html>
<html lang="en">
<head>
<meta charset="utf-8">
<title>Rosalind Thorpe Gardens – Business Card</title>
<link href="https://fonts.googleapis.com/css2?family=EB+Garamond:wght@400;500;700&display=swap" rel="stylesheet">
<style>
  :root {
    --teal-deep: #0b2a2e;
    --paper: #ffffff;
    --stripe-grey: #c3c6c9;
    --ink: #1a1a1a;
    --backdrop: #3b3a39;
  }
  html, body {
    margin: 0;
    padding: 0;
    width: 1200px;
    height: 900px;
    overflow: hidden;
    background: var(--backdrop);
    font-family: "EB Garamond", Georgia, serif;
  }
  .canvas {
    position: relative;
    width: 1200px;
    height: 900px;
  }
  .card {
    position: absolute;
    left: 280px;
    width: 640px;
    height: 366px;
    overflow: hidden;
    box-shadow: 0 10px 28px rgba(0,0,0,0.45);
  }
  .card--front { top: 64px; background: var(--teal-deep); }
  .card--back  { top: 470px; background: var(--paper); }

  .brand-seal {
    position: absolute;
    border-radius: 50%;
    display: flex;
    align-items: center;
    justify-content: center;
    text-align: center;
    box-sizing: border-box;
    font-weight: 500;
    letter-spacing: 0.12em;
    text-transform: uppercase;
    line-height: 1.25;
  }
  .card--front .brand-seal {
    left: 200px; top: 63px;
    width: 240px; height: 240px;
    border: 1.5px solid var(--paper);
    color: var(--paper);
    font-size: 25px;
  }
  .card--back .brand-seal {
    right: 42px; top: 18px;
    width: 140px; height: 140px;
    border: 1.2px solid var(--teal-deep);
    color: var(--teal-deep);
    font-size: 15px;
  }

  .wave { position: absolute; inset: 0; }

  .holder {
    position: absolute;
    left: 58px; top: 158px;
  }
  .holder__name {
    margin: 0;
    font-size: 25px;
    font-weight: 700;
    color: var(--teal-deep);
  }
  .holder__role {
    margin: 0 0 0 14px;
    font-size: 16px;
    color: var(--ink);
  }

  .contacts {
    position: absolute;
    left: 210px; top: 272px;
    margin: 0; padding: 0;
    list-style: none;
    color: var(--paper);
    font-size: 18px;
    line-height: 22px;
  }
  .contacts li { display: flex; align-items: center; gap: 6px; }
  .contacts svg { width: 14px; height: 14px; flex: none; }
</style>
</head>
<body>
<main class="canvas">

  <section class="card card--front" aria-label="Card front">
    <div class="brand-seal">Rosalind<br>Thorpe<br>Gardens</div>
  </section>

  <section class="card card--back" aria-label="Card back">
    <svg class="wave" viewBox="0 0 640 366" preserveAspectRatio="none" aria-hidden="true">
      <path fill="var(--stripe-grey)" d="M0,300 C150,262 250,212 400,202 C520,194 600,170 640,150 L640,366 L0,366 Z"/>
      <path fill="var(--paper)" d="M0,312 C150,274 255,222 405,212 C525,204 600,182 640,162 L640,366 L0,366 Z"/>
      <path fill="var(--teal-deep)" d="M0,320 C150,282 258,230 408,220 C528,212 600,192 640,172 L640,366 L0,366 Z"/>
      <path fill="var(--teal-deep)" d="M260,214 C330,195 390,188 440,185 C540,178 600,150 640,128 L640,140 C600,162 540,190 440,196 C380,200 320,205 260,214 Z"/>
    </svg>

    <div class="brand-seal">Rosalind<br>Thorpe<br>Gardens</div>

    <div class="holder">
      <p class="holder__name">Corinne Haldwick</p>
      <p class="holder__role">Owner</p>
    </div>

    <ul class="contacts">
      <li>
        <svg viewBox="0 0 16 16" aria-label="Phone" role="img"><path fill="#fff" d="M3 1h3l1 4-2 1.5a9 9 0 0 0 4.5 4.5L11 9l4 1v3c0 1-1 2-2 2A13 13 0 0 1 1 3c0-1 1-2 2-2z"/></svg>
        913-555-0147
      </li>
      <li>
        <svg viewBox="0 0 16 16" aria-label="Website" role="img"><circle cx="8" cy="8" r="7" fill="none" stroke="#fff" stroke-width="1.5"/><ellipse cx="8" cy="8" rx="3" ry="7" fill="none" stroke="#fff" stroke-width="1.2"/><path d="M1 8h14" stroke="#fff" stroke-width="1.2"/></svg>
        RosalindThorpeGardens.example
      </li>
      <li>
        <svg viewBox="0 0 16 16" aria-hidden="true"><rect x="2" y="2" width="12" height="12" fill="#fff"/></svg>
        Rosalind Thorpe Gardens
      </li>
      <li>
        <svg viewBox="0 0 16 16" aria-hidden="true"><rect x="2" y="2" width="12" height="12" fill="#fff"/></svg>
        @RosalindThorpeGardens
      </li>
    </ul>
  </section>

</main>
</body>
</html>
```